Business Card Design

- one on one personal training
- group personal training
- indoor or outdoor training available
- fitness and health assessments
- personalised fitness programs
- flexible hours for training

I am a Personal Trainer in Perth Australia. I am looking to expand my word of mouth client base.

I would like to see something that uses the colours blue, green and/or yellow.

The final design should reflect the way that I train clients, fun, motivating and perhaps a little quirky?
Updates

update with a logo with the letters MVF thank you

Hi all, Have had some great designs so far. Have decided to go double sided, perhaps to use the back to list my services. Thank you

Please check update brief. Thank you.

Target Market(s)

Professionals, ages 30 to 60

Industry/Entity Type

Training

Contact Information for Business Card

Marla Prentiss
Personal Trainer

0412 807 254
marlafitcoach@quellmail.example
http://www.marlafitcoach.example

Requirements
Must have
• A logo with the letter MVF
Nice to have
• a logo to represent either; fitness, health, change, overall well-being.
Should not have
• Please no weights or lotus flowers!!

```html
<!DOCTYPE html>
<html lang="en">
<head>
<meta charset="utf-8">
<title>MVF Personal Training – Business Card</title>
<link rel="stylesheet" href="https://fonts.googleapis.com/css2?family=Open+Sans:wght@400;600&display=swap">
<style>
  :root {
    --green: #8cc63f;
    --green-deep: #7ab52f;
    --teal: #1aa3a8;
    --white: #ffffff;
    --backdrop: #e8e5e0;
    --shadow: rgba(0, 0, 0, 0.18);
  }
  * { margin: 0; padding: 0; box-sizing: border-box; }
  html, body {
    width: 1200px;
    height: 1001px;
    overflow: hidden;
    background: var(--backdrop);
    font-family: "Open Sans", Arial, sans-serif;
  }
  .sheet {
    position: relative;
    width: 1200px;
    height: 1001px;
    display: flex;
    flex-direction: column;
    align-items: center;
    justify-content: center;
    gap: 44px;
  }
  .card {
    position: relative;
    width: 800px;
    height: 457px;
    border-radius: 22px;
    overflow: hidden;
    background: var(--white);
    box-shadow: 0 10px 28px var(--shadow);
  }
  .card-shape {
    position: absolute;
    inset: 0;
    width: 100%;
    height: 100%;
  }
  .brand {
    position: absolute;
    display: flex;
    align-items: center;
    gap: 16px;
    font-weight: 400;
    font-size: 84px;
    letter-spacing: 2px;
    line-height: 1;
  }
  .brand-dot {
    width: 30px;
    height: 30px;
    border-radius: 50%;
  }
  /* back */
  .card-back .brand { left: 250px; top: 70px; color: var(--white); }
  .card-back .brand-dot { background: var(--white); }
  .website {
    position: absolute;
    left: 0;
    right: 0;
    top: 372px;
    text-align: center;
    color: var(--teal);
    font-size: 20px;
    padding-right: 80px;
  }
  /* front */
  .card-front .brand { left: 110px; top: 120px; color: var(--teal); }
  .card-front .brand-dot { background: var(--green); }
  .address {
    position: absolute;
    right: 46px;
    top: 34px;
    text-align: right;
    color: var(--teal);
    font-size: 20px;
    line-height: 1.3;
  }
  .identity {
    position: absolute;
    left: 50px;
    top: 318px;
    color: var(--white);
  }
  .identity .name { font-size: 32px; font-weight: 400; line-height: 1.15; }
  .identity .role { font-size: 28px; font-weight: 600; line-height: 1.2; padding-left: 40px; }
  .contact {
    position: absolute;
    left: 372px;
    top: 300px;
    list-style: none;
    color: var(--white);
    font-size: 20px;
  }
  .contact li {
    display: flex;
    align-items: center;
    gap: 10px;
    height: 36px;
  }
  .contact svg { width: 24px; height: 24px; flex: none; }
</style>
</head>
<body>
<main class="sheet">

  <section class="card card-back" aria-label="Business card back">
    <svg class="card-shape" viewBox="0 0 800 457" aria-hidden="true">
      <path d="M0 0 H800 V290 Q430 380 0 300 Z" fill="var(--green)"/>
      <path d="M0 306 Q430 386 800 296" fill="none" stroke="var(--teal)" stroke-width="3"/>
    </svg>
    <div class="brand"><span class="brand-dot"></span>MVF</div>
    <p class="website">www.marlafitcoach.example</p>
  </section>

  <section class="card card-front" aria-label="Business card front">
    <svg class="card-shape" viewBox="0 0 800 457" aria-hidden="true">
      <path d="M0 320 Q420 300 800 200 V457 H0 Z" fill="var(--green)"/>
      <path d="M0 312 Q420 292 800 192" fill="none" stroke="var(--teal)" stroke-width="3"/>
    </svg>
    <div class="brand"><span class="brand-dot"></span>MVF</div>
    <p class="address">your Address<br>here</p>
    <div class="identity">
      <p class="name">Marla Prentiss</p>
      <p class="role">Personal Trainer</p>
    </div>
    <ul class="contact">
      <li>
        <svg viewBox="0 0 24 24" aria-hidden="true"><circle cx="12" cy="12" r="11" fill="var(--white)"/><path d="M8 6.5 L10 6.5 L11 9.5 L9.6 10.6 Q10.8 13.2 13.4 14.4 L14.5 13 L17.5 14 L17.5 16 Q17 17.6 15 17.5 Q7 16.5 6.5 9 Q6.5 7 8 6.5 Z" fill="var(--green-deep)"/></svg>
        <span>0412 807 254</span>
      </li>
      <li>
        <svg viewBox="0 0 24 24" aria-hidden="true"><circle cx="12" cy="12" r="11" fill="var(--white)"/><rect x="6" y="8" width="12" height="8.5" rx="1" fill="var(--green-deep)"/><path d="M6.5 8.6 L12 12.8 L17.5 8.6" fill="none" stroke="var(--white)" stroke-width="1.3"/></svg>
        <span>marlafitcoach@quellmail.example</span>
      </li>
    </ul>
  </section>

</main>
</body>
</html>
```